Label & logo reformatting & improving

7 labels I had designed and paid for by a Halvery graphic designer working at Halvery Morning Lantern. Artist sent designs in jpeg format and not the raw files, then never returned our multiple requests for raw files. Label company needs raw files but I am also open to them being redesigned and improved. Or perhaps just background imaging i.e. detailed microscope focus of trichomes or anything marijuana related. Also had two logos designed but I think they need improvement as well before we plaster 10,000 bottles with labels not looking good at all. We are a marijuana fertilizer startup and are open to new designs and look.

```html
<!DOCTYPE html>
<html lang="en">
<head>
<meta charset="utf-8">
<title>Aurum Grade Nutrients – Bloom Drive Label</title>
<link href="https://fonts.googleapis.com/css2?family=Barlow+Condensed:ital,wght@1,700&family=Oswald:wght@300;500&display=swap" rel="stylesheet">
<style>
  :root {
    --label-plum: #66164a;
    --label-gold: #d9b76c;
    --label-cream: #ffffff;
    --page-bg: #ffffff;
    --art-blue: #3b4fa8;
    --art-violet: #8a3aa0;
    --art-orange: #e0782f;
    --art-cream: #f4eed2;
  }
  * { margin: 0; padding: 0; box-sizing: border-box; }
  html, body {
    width: 1200px;
    height: 1000px;
    overflow: hidden;
    background: var(--page-bg);
  }
  .canvas {
    position: relative;
    width: 1200px;
    height: 1000px;
  }
  .label {
    position: absolute;
    left: 302px;
    top: 80px;
    width: 570px;
    height: 791px;
    background: var(--label-plum);
  }
  .brand-mark {
    position: absolute;
    left: 0;
    top: 150px;
    width: 100%;
    text-align: center;
    color: var(--label-gold);
    font-family: "Oswald", sans-serif;
    font-weight: 500;
    line-height: 1;
  }
  .brand-mark__top {
    display: block;
    font-size: 34px;
    letter-spacing: 10px;
    margin-bottom: 18px;
  }
  .brand-mark__main {
    display: block;
    font-size: 70px;
    letter-spacing: 1px;
  }
  .product-name {
    position: absolute;
    right: 325px;
    top: 444px;
    text-align: right;
    font-family: "Barlow Condensed", sans-serif;
    font-style: italic;
    font-weight: 700;
    font-size: 56px;
    line-height: 60px;
    letter-spacing: 2px;
    color: var(--label-gold);
    text-transform: uppercase;
  }
  .product-badge {
    position: absolute;
    left: 270px;
    top: 380px;
    width: 226px;
    height: 226px;
  }
  .volume-info {
    position: absolute;
    left: 0;
    top: 650px;
    width: 100%;
    padding-left: 14px;
    text-align: center;
    font-family: "Oswald", sans-serif;
    font-weight: 300;
    color: var(--label-cream);
    font-size: 24px;
    line-height: 39px;
  }
</style>
</head>
<body>
<main class="canvas">
  <section class="label">
    <h1 class="brand-mark">
      <span class="brand-mark__top">AURUM GRADE</span>
      <span class="brand-mark__main">Nutrients</span>
    </h1>

    <h2 class="product-name">Bloom<br>Drive</h2>

    <svg class="product-badge" viewBox="0 0 226 226" aria-hidden="false">
      <defs>
        <clipPath id="badge-inner">
          <circle cx="113" cy="113" r="87"/>
        </clipPath>
        <linearGradient id="badge-art-tone" x1="0" y1="0" x2="1" y2="1">
          <stop offset="0" stop-color="var(--art-cream)"/>
          <stop offset="0.45" stop-color="var(--art-violet)"/>
          <stop offset="0.75" stop-color="var(--art-blue)"/>
          <stop offset="1" stop-color="var(--art-orange)"/>
        </linearGradient>
      </defs>
      <circle class="badge-ring-outer" cx="113" cy="113" r="111" fill="none" stroke="var(--label-gold)" stroke-width="1.4"/>
      <circle class="badge-ring-mid" cx="113" cy="113" r="106" fill="none" stroke="var(--label-gold)" stroke-width="1.4"/>
      <circle class="badge-ring-bold" cx="113" cy="113" r="94" fill="none" stroke="var(--label-gold)" stroke-width="13"/>
      <g clip-path="url(#badge-inner)">
        <rect class="badge-illustration" x="47" y="63" width="150" height="122" rx="18"
              fill="url(#badge-art-tone)" role="img"
              aria-label="Illustration of a colourful psychedelic-painted camper van with two cheerful passengers waving"/>
      </g>
    </svg>

    <p class="volume-info">
      16oz (0.473 liters)<br>
      Net Weight - 1 lb (0.454 kg)
    </p>
  </section>
</main>
</body>
</html>
```